Business Card Design needed for start up company Halvora

In need of a new business card designed for a start up company based in Sydney, Halvora is a new start up innovative Company, our mission it to make property accessible for everyday Australian and to become the leading Real Estate platform in Australia. We want it to be fresh and clean.

Industry/Entity Type

Financial

Contact Information for Business Card

Section for Name
Section for Title

HALVORA - The Strength of Pooling
Mobile:
Direct:

Font styles to use
Sans Serif

Colors
33a6d7
0692cd
0255a3
ffffff

Requirements
Must have
• Logo, all business card details

```html
<!DOCTYPE html>
<html lang="en">
<head>
<meta charset="utf-8">
<title>Halvora Business Card</title>
<link rel="stylesheet" href="https://fonts.googleapis.com/css2?family=Jost:wght@400;500;600;700&display=swap">
<style>
  :root {
    --navy: #214176;
    --sky: #2a9fd8;
    --paper: #f4f4f4;
    --ink: #4a4a4a;
    --backdrop: #2b2b2b;
    --white: #ffffff;
  }
  * { margin: 0; padding: 0; box-sizing: border-box; }
  html, body { width: 1200px; height: 960px; overflow: hidden; }
  body {
    position: relative;
    background: var(--backdrop);
    font-family: "Jost", "Futura", sans-serif;
  }
  .card {
    position: absolute;
    width: 600px;
    height: 342px;
    border-radius: 18px;
    overflow: hidden;
  }
  .card-front { left: 302px; top: 124px; background: var(--paper); }
  .card-back { left: 299px; top: 493px; background: var(--navy); }

  .name-band {
    position: absolute;
    left: 0; top: 36px;
    width: 330px; height: 77px;
    background: var(--navy);
    padding: 18px 0 0 34px;
    color: var(--white);
  }
  .person-name { font-size: 21px; font-weight: 600; letter-spacing: 0.3px; line-height: 1.1; }
  .person-title { font-size: 15px; font-weight: 400; line-height: 1.2; }

  .brand {
    position: absolute;
    display: flex;
    align-items: center;
  }
  .brand-mark {
    border-radius: 50%;
    background: var(--sky);
    flex: none;
  }
  .brand-name { font-weight: 700; line-height: 1; white-space: nowrap; }

  .card-front .brand { left: 304px; top: 36px; height: 78px; }
  .card-front .brand-mark { width: 76px; height: 76px; border: 3px solid var(--white); margin-right: 6px; }
  .card-front .brand-name { font-size: 37px; letter-spacing: -0.5px; color: var(--navy); }

  .contact-row {
    position: absolute;
    left: 34px; top: 271px;
    display: flex;
    align-items: center;
    color: var(--ink);
    font-size: 15px;
    line-height: 19px;
  }
  .contact-address { width: 177px; }
  .contact-phones { width: 172px; padding-left: 24px; }
  .contact-web { padding-left: 32px; }
  .divider { width: 2px; height: 39px; background: var(--navy); flex: none; }
  .contact-line { display: flex; align-items: center; gap: 8px; }
  .contact-line svg { width: 13px; height: 13px; fill: var(--navy); flex: none; }

  .card-back .brand { left: 124px; top: 116px; }
  .card-back .brand-mark { width: 106px; height: 106px; margin-right: 10px; }
  .card-back .brand-name { font-size: 58px; letter-spacing: -0.5px; color: var(--sky); }
  .tagline {
    position: absolute;
    left: 0; right: 0; top: 285px;
    text-align: center;
    color: var(--white);
    font-size: 17px;
  }
</style>
</head>
<body>
  <section class="card card-front">
    <div class="name-band">
      <div class="person-name">MARA ELLISON</div>
      <div class="person-title">CEO/FOUNDER</div>
    </div>
    <div class="brand">
      <span class="brand-mark"></span>
      <span class="brand-name">HALVORA</span>
    </div>
    <div class="contact-row">
      <div class="contact-address">
        <div>42 Wattle Grove Road</div>
        <div>Sydney, NSW 2000</div>
      </div>
      <span class="divider"></span>
      <div class="contact-phones">
        <div class="contact-line">
          <svg viewBox="0 0 24 24"><path d="M6.6 10.8a15.1 15.1 0 0 0 6.6 6.6l2.2-2.2a1 1 0 0 1 1-.25 11.4 11.4 0 0 0 3.6.57 1 1 0 0 1 1 1V20a1 1 0 0 1-1 1A17 17 0 0 1 3 4a1 1 0 0 1 1-1h3.5a1 1 0 0 1 1 1c0 1.25.2 2.45.57 3.57a1 1 0 0 1-.25 1z"/></svg>
          <span>612 555 0148</span>
        </div>
        <div class="contact-line">
          <svg viewBox="0 0 24 24"><path d="M7 1h10a2 2 0 0 1 2 2v18a2 2 0 0 1-2 2H7a2 2 0 0 1-2-2V3a2 2 0 0 1 2-2zm0 3v14h10V4z"/></svg>
          <span>614 555 0273</span>
        </div>
      </div>
      <span class="divider"></span>
      <div class="contact-web">
        <div class="contact-line">
          <svg viewBox="0 0 24 24"><path d="M2 5h20v14H2zm2 2v.5l8 5 8-5V7l-8 5z"/></svg>
          <span>mara@halvora.au</span>
        </div>
        <div class="contact-line">
          <svg viewBox="0 0 24 24"><path d="M12 2a10 10 0 1 0 0 20 10 10 0 0 0 0-20zm-1 17.9A8 8 0 0 1 4.1 11H8v2l3 3zm6.9-2.5A2 2 0 0 0 16 16h-1v-3H9v-2h2V9h2V6.3a8 8 0 0 1 4.9 11.1z"/></svg>
          <span>www.halvora.au</span>
        </div>
      </div>
    </div>
  </section>

  <section class="card card-back">
    <div class="brand">
      <span class="brand-mark"></span>
      <span class="brand-name">HALVORA</span>
    </div>
    <p class="tagline">The Strength of Pooling</p>
  </section>
</body>
</html>
```